Roofing Contractor business card redesign

I want to redesign my business card with a fresh, eye catching concept

Target Market(s)

Residential Roofing Clients, potential employees, and subcontractors.

Industry/Entity Type

Business

Colors

Designer to choose colors to be used in the design.

Requirements
Nice to have
• I just want something that's more pleasing to the eye. You can use a combination of either / or of my logos.

```html
<!DOCTYPE html>
<html lang="en">
<head>
<meta charset="utf-8">
<title>Fair Hands Business Card</title>
<link rel="stylesheet" href="https://fonts.googleapis.com/css2?family=Ubuntu:wght@400;500;700&display=swap">
<style>
  :root {
    --brown: #4a1f16;
    --brown-dark: #3a1a14;
    --orange: #e8731c;
    --orange-deep: #e5621d;
    --yellow: #f5bd1a;
    --paper: #fbfbfa;
    --ink: #3d2a25;
    --bg: #e9e6e1;
  }
  * { box-sizing: border-box; margin: 0; padding: 0; }
  html, body { width: 1200px; height: 911px; overflow: hidden; }
  body {
    background: var(--bg);
    font-family: "Ubuntu", sans-serif;
    display: flex; flex-direction: column; align-items: center; justify-content: center;
    gap: 36px;
  }
  .card {
    position: relative; width: 700px; height: 400px;
    border-radius: 22px; overflow: hidden;
    box-shadow: 0 6px 18px rgba(0,0,0,.18);
  }

  /* Front */
  .card-front { background: var(--paper); }
  .front-art {
    position: absolute; right: 20px; top: 0; width: 400px; height: 330px;
    background: radial-gradient(ellipse at 55% 50%, rgba(232,115,28,.22), rgba(245,189,26,.12) 55%, rgba(250,250,248,0) 75%);
  }
  .brand { position: absolute; left: 48px; top: 56px; }
  .brand-row { display: flex; align-items: center; gap: 10px; }
  .brand-name { font-weight: 700; font-size: 50px; color: var(--brown); letter-spacing: -1px; line-height: 1; }
  .brand-dot { width: 40px; height: 40px; border-radius: 50%; background: var(--orange); }
  .brand-tag { font-weight: 700; font-size: 21px; color: var(--brown); margin-top: 6px; }
  .holder { position: absolute; right: 56px; top: 96px; text-align: right; }
  .holder-name { font-weight: 500; font-size: 27px; color: var(--ink); letter-spacing: .5px; }
  .holder-title { font-size: 19px; color: var(--orange); line-height: 1.35; }
  .contact { position: absolute; left: 48px; bottom: 40px; list-style: none; font-size: 17px; color: var(--ink); line-height: 1.5; }
  .contact li { display: flex; align-items: center; gap: 10px; }
  .contact svg { width: 15px; height: 15px; fill: var(--ink); flex: none; }
  .contact .gap { width: 15px; }

  /* Back */
  .card-back { background: linear-gradient(120deg, var(--orange-deep) 0%, var(--orange) 40%, var(--yellow) 100%); }
  .back-band {
    position: absolute; left: 0; right: 0; bottom: 0; height: 150px;
    background: var(--brown-dark);
    clip-path: polygon(55% 0, 100% 0, 100% 100%, 0 100%, 0 70%);
  }
  .back-brand { position: absolute; left: 44px; top: 46px; color: var(--brown); }
  .back-name { font-weight: 700; font-size: 54px; letter-spacing: -1px; line-height: 1; }
  .back-tag { font-weight: 700; font-size: 21px; margin-top: 6px; }
  .back-web { font-size: 17px; letter-spacing: 2px; margin-top: 8px; }
  .back-seal {
    position: absolute; right: 52px; top: 70px; width: 300px; height: 300px; border-radius: 50%;
    border: 8px solid #fff;
    background: radial-gradient(circle at 55% 45%, #f08a2a 0%, #e8731c 35%, #f5c23a 55%, var(--brown-dark) 80%);
  }
</style>
</head>
<body>
  <section class="card card-front">
    <div class="front-art" role="img" aria-label="Faint illustration of three contractors with tools"></div>
    <div class="brand">
      <div class="brand-row">
        <span class="brand-name">Fair</span>
        <span class="brand-dot"></span>
        <span class="brand-name">Hands</span>
      </div>
      <div class="brand-tag">General Contractors, Inc.</div>
    </div>
    <div class="holder">
      <div class="holder-name">SAM WHITLOCK</div>
      <div class="holder-title">Ridgeway Certified Roof Inspector</div>
      <div class="holder-title">Licensed Property Adjuster</div>
    </div>
    <ul class="contact">
      <li><span class="gap"></span>4410 Cedar Mill Road Suite 118</li>
      <li><span class="gap"></span>Plano, TX 75024</li>
      <li><svg viewBox="0 0 16 16"><path d="M3 1l3 3-2 2c1 2 3 4 5 5l2-2 3 3-2 2C7 14 2 9 1 3z"/></svg>(555) 214-3080</li>
      <li><svg viewBox="0 0 16 16"><path d="M4 1h8v14H4zM5.5 3v9h5V3z"/></svg>(555) 867-1290</li>
      <li><svg viewBox="0 0 16 16"><path d="M1 3h14v10H1zM2 4.5v.3l6 4 6-4v-.3z"/></svg>sam@fairhandstx.com</li>
      <li><svg viewBox="0 0 16 16"><circle cx="8" cy="8" r="7"/></svg>www.fairhandstx.com</li>
    </ul>
  </section>

  <section class="card card-back">
    <div class="back-band"></div>
    <div class="back-brand">
      <div class="back-name">Fair Hands</div>
      <div class="back-tag">General Contractors, Inc.</div>
      <div class="back-web">www.fairhandstx.com</div>
    </div>
    <div class="back-seal" role="img" aria-label="Circular illustration of three contractors holding hammers and tools"></div>
  </section>
</body>
</html>
```